Design the Taste: Help Us Cook Up a Fresh Brochure for Our Wholesale Food Brand!

Overview:
We are looking for a fresh, eye-catching brochure design for our wholesale food company. The brochure can be up to 6 pages and should be visually appealing while clearly presenting our products and services.

Reference:
Please use the attached previous brochure as a guide for layout and style inspiration.

Content Requirements:
The brochure must highlight our key food groups:

Frozen Entrées
Pizzas
Frozen Meals and Party Size
Dry goods and Pasta
Gift Baskets
Delicacies and Sweets
Can do private label
Additional Highlights:

We deliver to our customers.
All products are fresh and locally made in Nashville, TN.

Design Goals:

Modern, appetizing, and professional design

Easy to read and navigate
Should NOT say Brindle's Harbor Grocer and Bistro but brand colors should resemble our parent company Brindles Harbor Grocer and Bistro
Strong visual focus on our products
Also mention we can brand with clients information
Incorporate brand colors and style from previous brochure

Phone: (615) 902-3378
https://brindlesupplyandtrade.com/
use any pictures from this site: https://brindlesupplyandtrade.com/

use circle logo for Brindle's Harbor Fine Foods

Outstanding family dining and exquisite imported Italian delights.
Today, you’ll find our locally made dishes in markets, mini-marts, and corner stores across the city, making it easy for your clients to enjoy the taste of Brindle’s at home.

Alongside our prepared foods, we offer a curated selection of imported Italian goods, handcrafted gift baskets made in-house, and our signature marinara sauce, lovingly created from my Nona’s treasured recipes.

Use only our pictures of pizza, pasta, dry pasta, marina sauce, canolis, frozen entrees, frozen dishes and meat dishes provided in breif and on website. Can also use pictures from our facebook and instra gram
https://www.facebook.com/brindlesupply
https://www.instagram.com/brindle_supply/

Target Market(s)

Liquior stores, mini markets, gas stations and mini food places

Industry/Entity Type

Food

Font styles to use
Other font styles liked:
• Valadimir script and new times roman

Colors
59FF00
82FF00
B8FF75
E3FFCB
F4FFEA
EB3D1F
EC4F4E
F09395
F8D3D4
FCEDEE

Requirements
Must have
• Item sectiosn metnioned, logo, phone number and webaddress

```html
<!DOCTYPE html>
<html lang="en">
<head>
<meta charset="utf-8">
<title>Brindle's Harbor Fine Foods – Wholesale Catalogue</title>
<link rel="stylesheet" href="https://fonts.googleapis.com/css2?family=Bebas+Neue&family=Montserrat:wght@400;500;600;700;800&family=Libre+Baskerville:wght@700&display=swap">
<style>
  :root{
    --red:#d32a2b;
    --red-deep:#c21f22;
    --green:#0f7a3c;
    --green-bright:#17a04f;
    --paper:#f2efe9;
    --ink:#2b2b2b;
    --muted:#4a4a4a;
    --stage:#e4e4e4;
    --white:#ffffff;
  }
  *{margin:0;padding:0;box-sizing:border-box}
  html,body{width:1200px;height:3556px;overflow:hidden;background:var(--stage)}
  body{position:relative;font-family:'Montserrat',sans-serif;color:var(--ink)}
  .spread{position:absolute;left:50px;width:1100px;height:850px;background:var(--paper);overflow:hidden;box-shadow:0 6px 18px rgba(0,0,0,.18)}
  .spread--cover{top:618px}
  .spread--products{top:2088px}
  .abs{position:absolute}
  .photo{position:absolute;border:4px solid var(--white);box-shadow:0 2px 6px rgba(0,0,0,.2)}

  /* cover */
  .cover__band{left:399px;top:0;width:494px;height:850px;background:var(--red)}
  .cover__title{left:599px;top:40px;font-family:'Bebas Neue',sans-serif;font-size:70px;line-height:62px;color:var(--white)}
  .cover__title span{display:block;color:var(--green-bright)}
  .cover__sub{left:599px;top:190px;font-weight:600;font-size:17px;line-height:22px;color:var(--white)}
  .cover__url{left:599px;top:780px;font-size:16px;color:var(--white)}
  .logo{position:absolute;border-radius:50%;background:var(--white);border:3px solid var(--green);display:flex;align-items:center;justify-content:center;text-align:center}
  .logo__name{font-family:'Montserrat',sans-serif;font-weight:700;color:var(--red-deep);line-height:1.1}
  .logo--large{left:924px;top:47px;width:124px;height:124px}
  .logo--large .logo__name{font-size:15px}
  .logo--small{left:48px;top:523px;width:66px;height:66px;border-width:2px}
  .logo--small .logo__name{font-size:9px}

  .about__heading{left:47px;top:44px;font-weight:800;font-size:27px;color:var(--green)}
  .about__text{left:47px;top:88px;width:320px;font-size:12.3px;line-height:15.5px;color:var(--muted)}
  .about__text p+p{margin-top:12px}
  .contact__heading{left:47px;top:610px;font-weight:800;font-size:20px;color:var(--red)}
  .contact__list{left:47px;top:645px;list-style:none}
  .contact__list li{display:flex;align-items:flex-start;gap:8px;font-size:16px;line-height:20px;margin-bottom:17px}
  .contact__list li.phone{font-weight:700;font-size:19px}
  .contact__list svg{flex:none;margin-top:4px}

  /* products */
  .products__red{left:0;top:0;width:171px;height:850px;background:var(--red)}
  .products__green{left:934px;top:0;width:166px;height:850px;background:var(--green)}
  .products__heading{left:199px;top:44px;font-weight:800;font-size:26px;color:var(--red)}
  .products__heading span{color:var(--green)}
  .item__title{font-weight:800;font-size:19px;line-height:19px;text-transform:uppercase}
  .item__title--red{color:var(--red)}
  .item__title--green{color:var(--green)}
  .item__text{font-size:10.5px;line-height:13.5px;color:var(--muted);width:175px;margin-top:10px}
  .deliver{left:136px;top:737px;width:349px;height:38px;background:var(--green);color:var(--white);font-family:'Bebas Neue',sans-serif;font-size:28px;line-height:40px;padding-left:22px;white-space:nowrap}
  .van{left:48px;top:724px;width:90px;height:58px;background:linear-gradient(135deg,#f2f2ee,#d9d9d4);border-radius:8px;box-shadow:0 1px 4px rgba(0,0,0,.2);z-index:2}
  .url-dark{font-size:15.5px;color:var(--ink);top:780px}
  .private{left:598px;top:686px;font-family:'Libre Baskerville',serif;font-weight:700;font-size:19px;color:var(--green);letter-spacing:.5px}
  .fresh{left:598px;top:720px;width:333px;height:54px;background:var(--red);color:var(--white);font-weight:600;font-size:18px;line-height:21px;padding:6px 14px}
  .round-photo{position:absolute;border-radius:50%;border:4px solid var(--white);box-shadow:0 2px 6px rgba(0,0,0,.2)}
</style>
</head>
<body>

<section class="spread spread--cover" aria-label="Catalogue cover">
  <div class="abs cover__band"></div>

  <h2 class="abs about__heading">ABOUT US</h2>
  <div class="abs about__text">
    <p>Outstanding family dining and exquisite imported Italian delights. Today, you'll find our locally made dishes in markets, mini-marts, and corner stores across the city, making it easy for your clients to enjoy the taste of Brindle’s at home.</p>
    <p>Alongside our prepared foods, we offer a curated selection of imported Italian goods, handcrafted gift baskets made in-house, and our signature marinara sauce, lovingly created from my Nona’s treasured recipes.</p>
  </div>
  <div class="photo" style="left:50px;top:266px;width:427px;height:238px;background:linear-gradient(135deg,#e9e4dc 0%,#d9713f 40%,#c64a26 80%,#e6e2dc 100%)" role="img" aria-label="Baked ziti with melted mozzarella in a white oval dish"></div>

  <div class="logo logo--small"><span class="logo__name">Brindle's</span></div>
  <h3 class="abs contact__heading">CONTACT US</h3>
  <ul class="abs contact__list">
    <li class="phone"><svg width="14" height="14" viewBox="0 0 14 14"><circle cx="7" cy="7" r="7" fill="#0f7a3c"/><path d="M4.5 3.5l1.5 0 .6 2-1 .7a5 5 0 0 0 2.2 2.2l.7-1 2 .6v1.5c-3.5.3-6.3-2.5-6-6z" fill="#fff"/></svg>(615) 902-3378</li>
    <li><svg width="14" height="14" viewBox="0 0 14 14"><circle cx="7" cy="7" r="7" fill="#0f7a3c"/><rect x="3.5" y="4.5" width="7" height="5" fill="none" stroke="#fff"/><path d="M3.5 4.5l3.5 3 3.5-3" fill="none" stroke="#fff"/></svg>orders@brindlesupply.com</li>
    <li><svg width="14" height="14" viewBox="0 0 14 14"><circle cx="7" cy="7" r="7" fill="#0f7a3c"/><path d="M7 3a2.5 2.5 0 0 1 2.5 2.5C9.5 7.5 7 11 7 11S4.5 7.5 4.5 5.5A2.5 2.5 0 0 1 7 3z" fill="#fff"/><circle cx="7" cy="5.5" r="1" fill="#0f7a3c"/></svg>2840 Larkspur Ave Nashville,<br>TN 37211 United States</li>
    <li><svg width="14" height="14" viewBox="0 0 14 14"><circle cx="7" cy="7" r="7" fill="#0f7a3c"/><circle cx="7" cy="7" r="3.6" fill="none" stroke="#fff"/><path d="M3.4 7h7.2M7 3.4c-1.6 2-1.6 5.2 0 7.2M7 3.4c1.6 2 1.6 5.2 0 7.2" fill="none" stroke="#fff" stroke-width=".8"/></svg>brindlesupplyandtrade.com</li>
  </ul>

  <h1 class="abs cover__title">WHOLESALE<span>CATALOGUE</span></h1>
  <p class="abs cover__sub">Fresh &amp; Locally Handmade<br>Italian Take-n-Bake<br>Italian Market Imported Goods</p>
  <div class="logo logo--large"><span class="logo__name">Brindle's Harbor<br>Fine Foods</span></div>
  <div class="photo" style="left:551px;top:302px;width:497px;height:449px;background:radial-gradient(circle at 50% 55%,#d98b46 0%,#b5462a 45%,#7a2a18 75%,#3a2a22 100%)" role="img" aria-label="Tortellini in tomato cream sauce with spinach and grated parmesan"></div>
  <p class="abs cover__url">brindlesupplyandtrade.com</p>
</section>

<section class="spread spread--products" aria-label="Our products">
  <div class="abs products__red"></div>
  <div class="abs products__green"></div>

  <h2 class="abs products__heading">OUR <span>PRODUCT</span></h2>

  <div class="photo" style="left:47px;top:86px;width:276px;height:181px;background:linear-gradient(135deg,#6d4a2c,#e6d9b8 45%,#c9b48a 75%,#7b5a3a)" role="img" aria-label="Packaged dry pasta bags on a shelf"></div>
  <div class="abs" style="left:347px;top:133px">
    <h3 class="item__title item__title--red">Frozen<br>Entrées</h3>
    <p class="item__text">we offer a curated selection of imported Italian goods, handcrafted gift baskets made in-house</p>
  </div>

  <div class="photo" style="left:47px;top:304px;width:276px;height:182px;background:linear-gradient(135deg,#f0d8a8,#e3a878 55%,#c9673f)" role="img" aria-label="Pepperoni pizza close-up"></div>
  <div class="abs" style="left:347px;top:359px">
    <h3 class="item__title item__title--red">Pizzas</h3>
    <p class="item__text">we offer a curated selection of imported Italian goods, handcrafted gift baskets made in-house</p>
  </div>

  <div class="photo" style="left:47px;top:521px;width:276px;height:182px;background:linear-gradient(160deg,#d9dcd8,#a8aca8 45%,#d9c07a 75%,#c9ccc8)" role="img" aria-label="Foil trays of frozen baked ziti meals"></div>
  <div class="abs" style="left:347px;top:563px">
    <h3 class="item__title item__title--red">Frozen<br>Meals and<br>Party Size</h3>
    <p class="item__text">we offer a curated selection of imported Italian goods, handcrafted gift baskets made in-house</p>
  </div>

  <div class="abs deliver">WE DELIVER TO OUR CUSTOMERS.</div>
  <div class="abs van" role="img" aria-label="Delivery van illustration"></div>
  <p class="abs url-dark" style="left:188px">www.brindlesupplyandtrade.com</p>

  <div class="abs" style="left:598px;top:97px">
    <h3 class="item__title item__title--green">Dry Goods<br>and Pasta</h3>
    <p class="item__text">we offer a curated selection of imported Italian goods, handcrafted gift baskets made in-house</p>
  </div>
  <div class="photo" style="left:775px;top:48px;width:273px;height:181px;background:linear-gradient(135deg,#3a3a32,#d8a058 40%,#c9683a 70%,#e9e4dc)" role="img" aria-label="Baked pasta with ham and cheese"></div>

  <div class="abs" style="left:598px;top:315px">
    <h3 class="item__title item__title--green">Gift<br>Baskets</h3>
    <p class="item__text">Our specialty curated gift baskets are perfect for anyone who loves Italian cooking at home.</p>
  </div>
  <div class="photo" style="left:775px;top:264px;width:273px;height:182px;background:linear-gradient(135deg,#f4f2ee,#6a3a32 35%,#c43a2e 60%,#f0ece4 90%)" role="img" aria-label="Gift basket with pizza stone, oven mitt and sauce jar"></div>

  <div class="abs" style="left:598px;top:533px">
    <h3 class="item__title item__title--green">Delicacies<br>and Sweets</h3>
    <p class="item__text">we offer a curated selection of imported Italian goods, handcrafted gift baskets made in-house</p>
  </div>
  <div class="photo" style="left:775px;top:484px;width:273px;height:181px;background:linear-gradient(135deg,#8a8a66,#5a5a40 55%,#c9b58a)" role="img" aria-label="Tray of handmade meatballs"></div>

  <p class="abs private">WE CAN DO PRIVATE LABEL</p>
  <div class="abs fresh">All products are fresh and<br>locally made in Nashville, TN.</div>
  <div class="round-photo" style="left:933px;top:691px;width:114px;height:114px;background:linear-gradient(135deg,#efe2c8,#d39a5a 50%,#8a2a1e)" role="img" aria-label="Pizza with toppings, seen from above"></div>
  <p class="abs url-dark" style="left:598px">www.brindlesupplyandtrade.com</p>
</section>

</body>
</html>
```